Business Card Design

WE are looking for a premium quality Business Cards for a Law Firm . Copies of our current business card is attached.

Contact Information for Business Card

xyz

```html
<!DOCTYPE html>
<html lang="en">
<head>
<meta charset="utf-8">
<title>Harlow Lawyers – Business Card</title>
<link rel="stylesheet" href="https://fonts.googleapis.com/css2?family=Cinzel:wght@700&family=Arimo:wght@400;700&display=swap">
<style>
  :root {
    --green: #0f3a2a;
    --gold: #b8944f;
    --ink: #1c1c1c;
    --paper: #ffffff;
    --backdrop: #d9d9d9;
  }
  * { box-sizing: border-box; margin: 0; padding: 0; }
  html, body { width: 1200px; height: 800px; overflow: hidden; }
  body {
    background: var(--backdrop);
    font-family: "Arimo", Arial, sans-serif;
    color: var(--ink);
    position: relative;
  }
  .card {
    position: absolute;
    top: 245px;
    width: 540px;
    height: 310px;
    background: var(--paper);
    border-radius: 18px;
    overflow: hidden;
    box-shadow: 0 6px 18px rgba(0,0,0,0.12);
  }
  .card--front { left: 40px; }
  .card--back { left: 620px; }

  .brand-name {
    position: absolute;
    font-family: "Arimo", Arial, sans-serif;
    font-weight: 700;
    color: var(--green);
    line-height: 1;
    white-space: nowrap;
  }
  .card--front .brand-name { top: 40px; right: 34px; font-size: 22px; }
  .card--back .brand-name { top: 140px; right: 40px; width: 250px; text-align: center; font-size: 28px; }

  .person { position: absolute; left: 34px; top: 138px; }
  .person__name {
    font-family: "Cinzel", Georgia, serif;
    font-weight: 700;
    font-size: 21px;
    color: var(--green);
    letter-spacing: 0.02em;
  }
  .person__role { font-size: 12.5px; color: var(--gold); line-height: 1.35; margin-top: 4px; }

  .rule { position: absolute; left: 34px; right: 34px; top: 212px; height: 1px; background: var(--ink); }

  .contacts { position: absolute; left: 34px; top: 220px; list-style: none; font-size: 12.5px; line-height: 1.4; }
  .contacts li { display: flex; align-items: center; gap: 7px; }
  .contacts svg { width: 10px; height: 11px; fill: none; stroke: var(--green); stroke-width: 1.6; }
  .contacts .no-icon { padding-left: 17px; }

  .office-main { position: absolute; right: 34px; top: 220px; text-align: right; font-size: 12.5px; line-height: 1.4; font-style: normal; }

  .band { position: absolute; left: 0; right: 0; bottom: 0; height: 30px; background: var(--gold); }
  .band__green {
    position: absolute; left: 0; top: 0; bottom: 0; width: 62%;
    background: var(--green);
    clip-path: polygon(0 0, 100% 0, calc(100% - 16px) 100%, 0 100%);
  }
  .band__web { position: absolute; right: 34px; top: 8px; font-size: 12.5px; color: var(--ink); letter-spacing: 0.02em; }

  .offices { position: absolute; left: 30px; top: 26px; font-size: 12.5px; line-height: 1.3; }
  .office { font-style: normal; margin-bottom: 12px; }
  .office h3 { font-size: 13px; font-weight: 700; }
  .office b { font-weight: 700; }
</style>
</head>
<body>
  <section class="card card--front">
    <p class="brand-name">HARLOW LAWYERS</p>

    <div class="person">
      <h1 class="person__name">DANIEL MERCER</h1>
      <p class="person__role">Director &amp; Principal Solicitor<br>MBA, Juris Doctor</p>
    </div>

    <div class="rule"></div>

    <ul class="contacts">
      <li><svg viewBox="0 0 10 11"><path d="M2 1 C0 3 2 8 7 10 L9 8 L7 6 L5.5 7 C4 6 3 5 3 3.5 L4 2 Z"/></svg>+61 7 3000 1234</li>
      <li><svg viewBox="0 0 10 11"><rect x="1.5" y="1" width="7" height="9" rx="1"/></svg>+61 0400 123 456</li>
      <li class="no-icon">daniel@harlowlawyers.com.au</li>
    </ul>

    <address class="office-main">
      Level 3, Harlow House<br>
      48 Ridgeview Terrace<br>
      Brookfield, QLD 4000
    </address>

    <div class="band">
      <div class="band__green"></div>
      <span class="band__web">www.harlowlawyers.com.au</span>
    </div>
  </section>

  <section class="card card--back">
    <div class="offices">
      <address class="office">
        <h3>Melbourne</h3>
        Level 9, Collins Point<br>
        210 Queen Street<br>
        Melbourne, VIC 3000<br>
        <b>Phone :</b> +61 03 8000 7715
      </address>
      <address class="office">
        <h3>Sydney</h3>
        Level 15, Northgate Building<br>
        72 Station Street<br>
        Parramatta, NSW 2150<br>
        <b>Phone :</b> +61 02 8000 4411
      </address>
      <address class="office">
        <h3>Perth</h3>
        Level 28, Meridian Tower<br>
        95 Riverside Terrace<br>
        Perth, WA 6000<br>
        <b>Phone :</b> +61 08 6000 2290
      </address>
    </div>

    <p class="brand-name">HARLOW LAWYERS</p>
  </section>
</body>
</html>
```